Electrician Letterhead Design MVR

We need some letterhead for our bills and other papers.
Customer address is on the right side (Swiss format)
A4 format

Design should also be applicable on Cards

Target Market(s)

Private Customers, Small Business

Industry/Entity Type

Electrician

Other font styles liked:
• incised 901

Colors
00AB8E
00BBA5
67D7C9
C6EFE9
E9F9F6

```html
<!DOCTYPE html>
<html lang="de">
<head>
<meta charset="utf-8">
<title>MVR Letterhead</title>
<link href="https://fonts.googleapis.com/css2?family=Ubuntu:wght@400;500;700&display=swap" rel="stylesheet">
<style>
  :root {
    --teal-deep: #00AB8E;
    --teal: #00BBA5;
    --teal-light: #67D7C9;
    --teal-pale: #C6EFE9;
    --teal-mist: #E9F9F6;
    --ink: #2a2f33;
    --paper: #ffffff;
    --backdrop: #e4e6e7;
  }
  * { margin: 0; padding: 0; box-sizing: border-box; }
  html, body {
    width: 1200px;
    height: 800px;
    overflow: hidden;
    background: var(--backdrop);
    font-family: "Ubuntu", sans-serif;
  }
  .letterhead {
    position: absolute;
    left: 340px;
    top: 32px;
    width: 520px;
    height: 736px;
    background: var(--paper);
    box-shadow: 0 6px 24px rgba(0,0,0,0.12);
    overflow: hidden;
  }
  .brand {
    position: absolute;
    left: 46px;
    top: 60px;
  }
  .brand-name {
    display: flex;
    align-items: center;
    gap: 10px;
    font-weight: 700;
    font-size: 46px;
    line-height: 1;
    color: var(--teal-deep);
    letter-spacing: 1px;
  }
  .brand-square {
    width: 18px;
    height: 18px;
    background: var(--teal-deep);
  }
  .brand-tagline {
    margin-top: 6px;
    font-size: 11px;
    font-weight: 500;
    color: var(--ink);
    letter-spacing: 0.3px;
  }
  .contact-list {
    position: absolute;
    right: 40px;
    top: 40px;
    list-style: none;
  }
  .contact-item {
    display: flex;
    align-items: center;
    gap: 7px;
    font-size: 10px;
    line-height: 15px;
    color: var(--ink);
  }
  .contact-icon {
    width: 10px;
    height: 10px;
    flex: none;
  }
  .footer-rule {
    position: absolute;
    left: 0;
    bottom: 62px;
    width: 520px;
    height: 6px;
    background: var(--teal-pale);
  }
  .footer-band {
    position: absolute;
    left: 0;
    bottom: 0;
    width: 520px;
    height: 56px;
    background: var(--teal);
    display: flex;
    align-items: center;
    justify-content: flex-end;
    padding-right: 34px;
  }
  .footer-address {
    font-size: 12px;
    color: var(--paper);
    letter-spacing: 0.2px;
  }
</style>
</head>
<body>
  <article class="letterhead">
    <header class="brand">
      <div class="brand-name"><span>MVR</span><span class="brand-square"></span></div>
      <div class="brand-tagline">Elektrotechnik Mauler GmbH</div>
    </header>

    <ul class="contact-list">
      <li class="contact-item">
        <svg class="contact-icon" viewBox="0 0 10 10"><circle cx="5" cy="5" r="5" fill="var(--teal-deep)"/><path d="M3.3 2.6l1 1-0.6 0.7a3 3 0 0 0 2 2l0.7-0.6 1 1-0.8 0.8C4.6 7.3 2.7 5.4 2.5 3.4z" fill="#fff"/></svg>
        +01-2345-678901
      </li>
      <li class="contact-item">
        <svg class="contact-icon" viewBox="0 0 10 10"><circle cx="5" cy="5" r="5" fill="var(--teal-deep)"/><rect x="3" y="2.5" width="4" height="5" rx="0.6" fill="#fff"/></svg>
        +01-2345-6789012
      </li>
      <li class="contact-item">
        <svg class="contact-icon" viewBox="0 0 10 10"><circle cx="5" cy="5" r="5" fill="var(--teal-deep)"/><rect x="2.5" y="3.2" width="5" height="3.6" fill="#fff"/><path d="M2.5 3.2L5 5.2 7.5 3.2" stroke="var(--teal-deep)" stroke-width="0.6" fill="none"/></svg>
        info@maulerelektro.com
      </li>
      <li class="contact-item">
        <svg class="contact-icon" viewBox="0 0 10 10"><circle cx="5" cy="5" r="5" fill="var(--teal-deep)"/><circle cx="5" cy="5" r="2.6" stroke="#fff" stroke-width="0.7" fill="none"/><path d="M2.4 5h5.2M5 2.4v5.2" stroke="#fff" stroke-width="0.6"/></svg>
        www.maulerelektro.com
      </li>
    </ul>

    <div class="footer-rule"></div>
    <footer class="footer-band">
      <p class="footer-address">Suite 102 Street name, State, Zip 2034, Country</p>
    </footer>
  </article>
</body>
</html>
```